Design my site www.brieflyledger.com

So here is what I am thinking in terms of design:

https://plenvo.com

https://www.skyluxair.com

http://kalvex.com/harbor-plaza-tower/

I want the theme to be white and blue (royal blue). I attached a paint picture of what I would like the site to look like in terms of placing the text. Generally, what I like about the sites above is that they are simple, you can navigate easily and have some kind of idea of what's going on by looking at the center (picture and motto). Let's establish a clear understanding of how the functional part of the site would look like. Please see the picture attached.

I want to keep it simple: On top would be the Name 'BRIEFLY ledger", somewhere to the right on top on the page would be 'Sign in" button.

In the center would be a picture (maybe a video) with the Motto (on top of it all in capital) OBSERVE NAVIGATE DECIDE and below would be the "sign up now"

Below the picture (like on kalvex.com site) or to the left on top of the page would be "About Us', "Press" "Contact Us' buttons.

Then once the user gets to his page his got 3 tabs " Press Headlines", "Events", " Briefings".

we would keep the same format I only have on the site, but separate for every Tab.

I do not want the user to get distracted. I also want him to be able to access the page though mobile phone and be able to get automatic updates just like Zorvan Pings without having to sign in daily.

The landing page must be minimalist yet with business/corporate feel where users can navigate easily and a "what you see is what you get" approach. You want an image or video (personally I prefer the video.. it does capture the users attention instantly, as long as it is an interesting video), with your taglines in it.

Sections available to public: About Us, Contact Us, Landing Page with Signup Option

Private: Public Sections + User Account Page, Tabs for (Events, Press Headlines, Briefings)

Target Market(s)

PR/media monitoring/diplomatic community

Coding

Coded - Design and coding required

Number of Pages Required

1 page

Font styles to use
Serif
Sans Serif

Colors
0255a3
ec1f27

Requirements
Must have
• a simple landing page, that is user friendly.
Nice to have
• a video with the explanation of how to navigate the site
Should not have
• too many colors, graphs etc.

```html
<!DOCTYPE html>
<html lang="en">
<head>
<meta charset="utf-8">
<title>BRIEFLY ledger — Press Headlines</title>
<link href="https://fonts.googleapis.com/css2?family=Raleway:ital,wght@0,400;0,500;0,600;0,700;0,800;1,400;1,500;1,600&display=swap" rel="stylesheet">
<style>
  :root {
    --royal: #0255a3;
    --royal-light: #0a8ade;
    --red: #ec1f27;
    --header-bg: #f2f2f2;
    --footer-bg: #383838;
    --footer-text: #c9c9c9;
    --text: #4a4a4a;
    --muted: #7a7a7a;
    --border: #dcdcdc;
    --date-bg: #f4f4f4;
    --white: #ffffff;
  }
  * { box-sizing: border-box; margin: 0; padding: 0; }
  html, body { width: 1200px; height: 738px; overflow: hidden; }
  body {
    position: relative;
    background: var(--white);
    font-family: "Raleway", Arial, sans-serif;
    color: var(--text);
  }

  .site-header {
    position: absolute; top: 0; left: 0;
    width: 1200px; height: 75px;
    background: var(--header-bg);
  }
  .brand {
    position: absolute; left: 75px; top: 16px;
    display: flex; align-items: center; gap: 10px;
    font-size: 32px; font-weight: 700; line-height: 40px;
    color: var(--royal); letter-spacing: 0.3px;
  }
  .brand__mark {
    width: 14px; height: 14px; background: var(--royal);
  }
  .sign-in {
    position: absolute; left: 1015px; top: 18px;
    width: 111px; height: 40px; border-radius: 20px;
    background: var(--royal); color: var(--white);
    font-size: 13px; font-weight: 700; letter-spacing: 0.3px;
    display: flex; align-items: center; justify-content: center;
    text-decoration: none;
  }

  .tabs { position: absolute; top: 98px; left: 0; width: 1200px; }
  .tab {
    position: absolute; top: 0;
    width: 283px; height: 58px; border-radius: 29px;
    background: linear-gradient(to bottom, var(--royal-light), var(--royal));
    color: var(--white);
    font-size: 19px; font-weight: 700; letter-spacing: 0.2px;
    display: flex; align-items: center; justify-content: center; gap: 10px;
    text-decoration: none;
  }
  .tab svg { width: 19px; height: 19px; fill: var(--white); }
  .tab--press { left: 130px; }
  .tab--events { left: 459px; }
  .tab--briefings { left: 787px; }
  .tab--active::after {
    content: ""; position: absolute; left: 50%; bottom: -12px;
    transform: translateX(-50%);
    border-left: 13px solid transparent; border-right: 13px solid transparent;
    border-top: 13px solid var(--royal);
  }

  .headline-panel {
    position: absolute; left: 75px; top: 162px;
    width: 1051px; height: 402px;
    border: 1px solid var(--border); border-radius: 4px;
  }
  .headline {
    position: absolute; left: 30px;
    width: 1000px; height: 130px;
  }
  .headline:nth-child(1) { top: 45px; }
  .headline:nth-child(2) { top: 220px; }

  .date-badge {
    position: absolute; left: 0; top: 0;
    width: 87px; height: 111px;
    border: 1px solid var(--border); border-radius: 3px;
    background: var(--date-bg); overflow: hidden; text-align: center;
  }
  .date-badge__month {
    height: 39px; background: var(--red); color: var(--white);
    font-size: 15px; font-weight: 600; line-height: 39px;
  }
  .date-badge__day {
    color: var(--royal); font-size: 42px; font-weight: 700; line-height: 44px; margin-top: 4px;
  }
  .date-badge__year {
    color: var(--royal); font-size: 14px; font-weight: 700; line-height: 16px;
  }

  .headline__body { position: absolute; left: 121px; top: 0; width: 880px; }
  .headline__title {
    color: var(--royal); font-size: 19.5px; font-weight: 700; line-height: 24px;
    letter-spacing: 0.1px;
  }
  .headline__meta {
    margin-top: 7px; display: flex; align-items: center;
    font-size: 13.5px; font-style: italic; color: var(--muted);
  }
  .headline__meta .label { color: var(--red); margin: 0 4px 0 6px; }
  .headline__meta svg { width: 11px; height: 12px; fill: var(--red); }
  .headline__meta .sep { color: var(--red); margin: 0 12px; font-style: normal; }
  .headline__excerpt {
    margin-top: 14px; font-size: 13.8px; line-height: 24px; color: var(--text);
    width: 850px;
  }

  .site-footer {
    position: absolute; left: 0; top: 658px;
    width: 1200px; height: 80px; background: var(--footer-bg);
  }
  .copyright {
    position: absolute; left: 76px; top: 35px;
    font-size: 11px; font-weight: 600; color: var(--footer-text); letter-spacing: 0.3px;
  }
  .social {
    position: absolute; right: 74px; top: 33px;
    display: flex; gap: 16px; list-style: none;
    font-size: 11px; font-weight: 600; color: var(--footer-text);
  }
</style>
</head>
<body>
  <header class="site-header">
    <div class="brand"><span class="brand__mark"></span>BRIEFLY ledger</div>
    <a class="sign-in" href="#">SIGN - IN</a>
  </header>

  <nav class="tabs">
    <a class="tab tab--press tab--active" href="#">
      <svg viewBox="0 0 20 20" aria-hidden="true"><path d="M3 4h8v2H5v9h9v-6h2v8H3z"/><path d="M15.5 1.5l3 3-8 8H7.5v-3z"/></svg>
      PRESS HEADLINES
    </a>
    <a class="tab tab--events" href="#">
      <svg viewBox="0 0 20 20" aria-hidden="true"><path d="M2 4h16v15H2zM4 8v9h12V8z"/><rect x="5" y="1" width="2" height="5"/><rect x="13" y="1" width="2" height="5"/><path d="M5 9h2v2H5zm4 0h2v2H9zm4 0h2v2h-2zM5 13h2v2H5zm4 0h2v2H9zm4 0h2v2h-2z"/></svg>
      EVENTS
    </a>
    <a class="tab tab--briefings" href="#">
      <svg viewBox="0 0 20 20" aria-hidden="true"><path d="M4 1h8l5 5v13H4z" /><path d="M6 9h8v1.5H6zm0 3h8v1.5H6zm0 3h8v1.5H6z" fill="#0a6fc4"/></svg>
      BRIEFINGS
    </a>
  </nav>

  <main class="headline-panel">
    <article class="headline">
      <div class="date-badge">
        <div class="date-badge__month">JUNE</div>
        <div class="date-badge__day">25</div>
        <div class="date-badge__year">2016</div>
      </div>
      <div class="headline__body">
        <h2 class="headline__title">VESTIBULUM ANTE IPSUM PRIMIS IN FAUCIBUS ORCI LUCTUS ET ULTRICES....</h2>
        <div class="headline__meta">
          <svg viewBox="0 0 12 12"><path d="M3 0h8v9H3.5a1 1 0 0 0 0 2H11v1H3.5A2.2 2.2 0 0 1 1.3 10V2A2 2 0 0 1 3 0z"/></svg><span class="label">Keyword:</span>Suspendisse lobortis turpis
          <span class="sep">|</span>
          <svg viewBox="0 0 12 12"><path d="M2 0h5l3 3v9H2z"/></svg><span class="label">Source:</span>Suspendisse
          <span class="sep">|</span>
          <svg viewBox="0 0 12 12"><path d="M1 2h10v10H1zM2 5v6h8V5z"/><rect x="3" y="0" width="1.5" height="3"/><rect x="7.5" y="0" width="1.5" height="3"/></svg><span class="label">Date:</span>June 25, 2016
        </div>
        <p class="headline__excerpt">Duis aliquam nibh a dui iaculis viverra id a velit. Vivamus egestas risus in magna varius commodo. Sed semper viverra egestas.<br>Etiam pretium porttitor lectus, vel ornare neque porta volutpat. Aenean a nibh eget turpis vehicula tempus ac sed massa. Vestibulum dolor nulla, ultrices ac tincidunt sed, laoreet non est....</p>
      </div>
    </article>

    <article class="headline">
      <div class="date-badge">
        <div class="date-badge__month">JUNE</div>
        <div class="date-badge__day">25</div>
        <div class="date-badge__year">2016</div>
      </div>
      <div class="headline__body">
        <h2 class="headline__title">VESTIBULUM ANTE IPSUM PRIMIS IN FAUCIBUS ORCI LUCTUS ET ULTRICES....</h2>
        <div class="headline__meta">
          <svg viewBox="0 0 12 12"><path d="M3 0h8v9H3.5a1 1 0 0 0 0 2H11v1H3.5A2.2 2.2 0 0 1 1.3 10V2A2 2 0 0 1 3 0z"/></svg><span class="label">Keyword:</span>Suspendisse lobortis turpis
          <span class="sep">|</span>
          <svg viewBox="0 0 12 12"><path d="M2 0h5l3 3v9H2z"/></svg><span class="label">Source:</span>Suspendisse
          <span class="sep">|</span>
          <svg viewBox="0 0 12 12"><path d="M1 2h10v10H1zM2 5v6h8V5z"/><rect x="3" y="0" width="1.5" height="3"/><rect x="7.5" y="0" width="1.5" height="3"/></svg><span class="label">Date:</span>June 25, 2016
        </div>
        <p class="headline__excerpt">Duis aliquam nibh a dui iaculis viverra id a velit. Vivamus egestas risus in magna varius commodo. Sed semper viverra egestas.<br>Etiam pretium porttitor lectus, vel ornare neque porta volutpat. Aenean a nibh eget turpis vehicula tempus ac sed massa. Vestibulum dolor nulla, ultrices ac tincidunt sed, laoreet non est....</p>
      </div>
    </article>
  </main>

  <footer class="site-footer">
    <p class="copyright">COPYRIGHT © 2016. BRIEFLY LEDGER. ALL RIGHT RESERVED</p>
    <ul class="social">
      <li>Fenlo</li>
      <li>Chirpo</li>
      <li>Plusra</li>
      <li>Snapvo</li>
      <li>Vidora</li>
    </ul>
  </footer>
</body>
</html>
```